Kestrelway Financial Plans

I am looking for a complete resdesign of my small financial presentation. This is a Word Doc/PDF that I print off when meeting with people in private. I often present my "two pager" that I have been using for years and years. It tells them the basics of what I do, how I help people and foundational financial principles.

I have recently gone out on my own in business and have completely rebranded. This presentation is my most used tool, so it is the first of many things I would like to redo. I am hoping it will somehow coordinate with the colors of my business, not necessarily the EXACT same 3 colors everywhere, but have the design colors compliment.

I've uploaded all my logo designs, as well as the current "two-pager". I am not against it going to 3 pages if needed. As it will still land on 2 pages with duplex printing.

It has always been VERY simple. I am wanting it built into a more professional and design specific format, to show off my branding, without being over cluttered.

I am completely open to ANY graphics changes. Obviously some are very novice, the house on the last page has always been overly simplified.

```html
<!DOCTYPE html>
<html lang="en">
<head>
<meta charset="utf-8">
<title>Kestrelway Financial Plans – Two Pager</title>
<link href="https://fonts.googleapis.com/css2?family=Montserrat:wght@300;400;500;600;700;800&display=swap" rel="stylesheet">
<style>
:root{
  --navy:#0f1722;
  --green:#1b9b3a;
  --green-light:#e3f4e7;
  --backdrop:#cccacb;
  --white:#ffffff;
  --red:#b3121b;
  --partner:#a9cdeb;
  --partner-ink:#1d3557;
  --pill-grey:#ececec;
}
*{box-sizing:border-box;margin:0;padding:0}
html,body{width:1200px;height:779px;overflow:hidden;background:var(--backdrop);font-family:'Montserrat',sans-serif;color:var(--navy)}
.page{position:absolute;top:37px;width:545px;height:705px;background:var(--white);overflow:hidden}
.page--left{left:35px}
.page--right{left:607px}
.abs{position:absolute}
.header-shapes{position:absolute;left:0;top:0}
.brand{position:absolute;left:34px;top:13px;color:var(--white);text-align:center;white-space:nowrap}
.brand__name{font-size:17px;font-weight:700;letter-spacing:.2px;line-height:20px}
.brand__sub{font-size:6.2px;font-weight:700;letter-spacing:1.2px;display:flex;align-items:center;gap:4px;justify-content:center;white-space:nowrap;margin-top:1px}
.brand__sub::before,.brand__sub::after{content:"";width:12px;height:1px;background:var(--white)}
.section-title{position:absolute;font-size:16.5px;letter-spacing:.3px;white-space:nowrap;display:flex;align-items:center;gap:8px;line-height:20px}
.section-title b{font-weight:700}
.section-title span{font-weight:300}
.section-title .rule{width:17px;height:1.4px;background:currentColor}

/* challenge pills */
.pill{position:absolute;top:91px;width:103px;height:208px;border:1px solid var(--green);border-radius:52px;text-align:center}
.pill__ring{position:absolute;left:10px;top:6px;width:81px;height:81px;border-radius:50%;background:var(--navy);display:flex;align-items:center;justify-content:center}
.pill__core{width:54px;height:54px;border-radius:50%;background:var(--green);display:flex;align-items:center;justify-content:center}
.pill__title{position:absolute;top:94px;width:100%;font-size:11.5px;font-weight:600}
.pill__body{position:absolute;top:114px;left:6px;right:6px;font-size:4.3px;line-height:6.2px;color:#444}
.pill__body p+p{margin-top:6px}

/* services band */
.band{position:absolute;left:0;top:326px;width:545px;height:136px;background:var(--green)}
.service{position:absolute;top:55px;width:70px;margin-left:-35px;text-align:center;color:var(--white)}
.service__icon{width:51px;height:51px;margin:0 auto;border-radius:50%;background:var(--white);border:2.5px solid var(--white);box-shadow:inset 0 0 0 1.5px var(--navy);display:flex;align-items:center;justify-content:center}
.service__label{margin-top:6px;font-size:5.6px;font-weight:700;line-height:6.4px}

/* how section */
.tag{position:absolute;height:24px;border-radius:12px;background:var(--navy);color:var(--white);font-size:10.5px;font-weight:500;display:flex;align-items:center;justify-content:center}
.savings-label{position:absolute;left:179px;top:587px;font-size:10.5px;font-weight:500}
.goals{position:absolute;left:78px;top:607px;width:244px;height:46px;border-radius:23px;background:var(--pill-grey);display:grid;grid-template-columns:110px 110px;padding:7px 0 0 15px;row-gap:4px}
.goal{font-size:8.4px;font-weight:500;display:flex;align-items:center;gap:4px;white-space:nowrap}
.goal i{width:7px;height:7px;border-radius:50%;background:var(--green);display:inline-block;position:relative}
.goal i::after{content:"";position:absolute;left:1.5px;top:2px;width:2px;height:2px;border-top:1px solid #fff;border-right:1px solid #fff;transform:rotate(45deg)}
.partner{position:absolute;height:28px;border-radius:9px;background:var(--partner);border:1px solid #8fb9dd;display:flex;align-items:center;justify-content:center;font-size:8.2px;font-weight:700;color:var(--partner-ink);white-space:nowrap}
.partner--c1{left:352px;width:78px}
.partner--c2{left:435px;width:83px}

/* rule of 72 */
.rule-col{position:absolute;top:113px;width:117px}
.rule-col__head{font-size:7.6px;font-weight:500;text-align:center;line-height:10.5px;height:33px}
.growth{background:var(--navy);border-radius:7px;overflow:hidden;color:var(--white);padding-bottom:7px}
.growth__head,.growth__row{display:flex;justify-content:space-between;align-items:center;padding:0 7px 0 7px;font-size:7.8px}
.growth__head{height:23px;background:var(--green);font-weight:500}
.growth__row{height:17px;font-weight:500}
.growth__row span:first-child{padding-left:7px}

/* taxes */
.tax-board{position:absolute;left:33px;top:377px;width:477px}
.tax-cols{position:absolute;left:0;top:17px;width:477px;height:133px;display:grid;grid-template-columns:repeat(4,1fr)}
.tax-col{color:var(--white);text-align:center;border-right:.5px solid #2c3a4a;padding:4px 6px 0}
.tax-col:last-child{border-right:none}
.tax-col__title{display:inline-block;font-size:9.5px;font-weight:600;padding-bottom:2px;border-bottom:1.2px solid var(--green)}
.tax-col__body{margin-top:14px;font-size:8px;font-weight:500;line-height:14px}
.tax-col__body p+p{margin-top:14px}
.tax-col__body.tight p+p{margin-top:7px}
.tax-result{position:absolute;left:0;top:150px;width:477px;height:23px;background:var(--white);display:grid;grid-template-columns:repeat(4,1fr);border-left:1px solid var(--navy);border-right:1px solid var(--navy)}
.tax-result div{display:flex;align-items:center;justify-content:center;font-size:9px;font-weight:600;color:var(--red);border-right:.5px solid #d0d0d0}
.tax-result div:last-child{border-right:none}
.tax-protect{position:absolute;left:0;top:173px;width:477px;height:67px;background:var(--green);border:3px solid var(--navy);border-top:none;display:grid;grid-template-columns:1fr 1fr;color:var(--white);font-size:9.3px;font-weight:500;text-align:center;line-height:14px;align-items:center}
</style>
</head>
<body>

<!-- ================= LEFT PAGE ================= -->
<section class="page page--left">
  <svg class="header-shapes" width="545" height="80" viewBox="0 0 545 80">
    <polygon points="0,0 545,0 545,8 0,72" fill="var(--navy)"/>
    <polygon points="283,26 545,0 545,72" fill="var(--green)"/>
  </svg>
  <div class="brand">
    <div class="brand__name">KESTRELWAY</div>
    <div class="brand__sub">FINANCIAL PLANS</div>
  </div>

  <h1 class="section-title" style="left:128px;top:50px">
    <i class="rule"></i><b>THE FINANCIAL</b><span>CHALLENGE</span><i class="rule"></i>
  </h1>

  <article class="pill" style="left:101px">
    <div class="pill__ring"><div class="pill__core">
      <svg width="30" height="30" viewBox="0 0 30 30" fill="none" stroke="#fff" stroke-width="1.4"><circle cx="12" cy="12" r="9"/><path d="M12 6v6l4 3"/><rect x="16" y="18" width="10" height="9" rx="2"/><path d="M21 20v5"/></svg>
    </div></div>
    <h2 class="pill__title">SAVINGS</h2>
    <div class="pill__body">
      <p>49% Of Canadian Employees Live Paycheque To Paycheque. 25% Cannot Cover An Unexpected $500 Expense. - National Survey (Feb 2023)</p>
      <p>25% Of Canadians Need To Access Retirement Savings Early. 20% Have No Savings. 39% Aged 55-65 Hold Less Than $5,000. - Federal Report (June 2023)</p>
    </div>
  </article>

  <article class="pill" style="left:221px">
    <div class="pill__ring"><div class="pill__core">
      <svg width="32" height="30" viewBox="0 0 32 30" fill="none" stroke="#fff" stroke-width="1.4"><path d="M12 3a9 9 0 1 0 9 9h-9z"/><path d="M15 1v8h8a8 8 0 0 0-8-8z"/><rect x="13" y="19" width="17" height="8" rx="1.5"/><path d="M16 23h11"/></svg>
    </div></div>
    <h2 class="pill__title">DEBT</h2>
    <div class="pill__body">
      <p>The Average Canadian Has $22,131 In Consumer Debt, Which Excludes Mortgages. - Credit Bureau (Aug 2024)</p>
      <p>Over 55% Of Canadians Hold Credit Card Debt And Total Household Debt Has Increased To $2.52 Trillion, Including Mortgage And Non-Mortgage Loans. - Banking Assoc. (Aug 2024)</p>
    </div>
  </article>

  <article class="pill" style="left:341px">
    <div class="pill__ring"><div class="pill__core">
      <svg width="30" height="30" viewBox="0 0 30 30" fill="none" stroke="#fff" stroke-width="1.4"><path d="M15 3l8 3v6c0 5-4 8-8 9-4-1-8-4-8-9V6z"/><path d="M11 12l3 3 5-5"/><path d="M3 20l5 5h5M27 20l-5 5h-5"/></svg>
    </div></div>
    <h2 class="pill__title">INSURANCE</h2>
    <div class="pill__body">
      <p>45% Of Canadians Do Not Have Individual Life Insurance, But 48% Say Their Families Would Face Financial Trouble Within 6 Months Of Losing Someone. - Industry Study (Apr 2023)</p>
      <p>2 In 5 Canadians Will Be Diagnosed With Cancer Or Another Critical Illness During Their Lifetime. - Health Data Canada (June 2024)</p>
    </div>
  </article>

  <section class="band">
    <h2 class="section-title" style="left:79px;top:20px;color:var(--white)">
      <i class="rule"></i><b>WHO ARE WE AND</b><span>WHAT DO WE DO?</span><i class="rule"></i>
    </h2>
    <div class="service" style="left:81px"><div class="service__icon"><svg width="24" height="24" viewBox="0 0 24 24" fill="none" stroke="var(--navy)" stroke-width="1.3"><circle cx="12" cy="12" r="6"/><path d="M12 9v6M2 7h6M16 17h6M5 4l-3 3 3 3M19 14l3 3-3 3"/></svg></div><div class="service__label">CASH FLOW</div></div>
    <div class="service" style="left:155px"><div class="service__icon"><svg width="24" height="24" viewBox="0 0 24 24" fill="none" stroke="var(--navy)" stroke-width="1.3"><path d="M12 2l8 3v7c0 5-4 8-8 10-4-2-8-5-8-10V5z"/><path d="M8 12l3 3 5-5"/></svg></div><div class="service__label">CASH FLOW<br>PROTECTION</div></div>
    <div class="service" style="left:229px"><div class="service__icon"><svg width="24" height="24" viewBox="0 0 24 24" fill="none" stroke="var(--navy)" stroke-width="1.3"><circle cx="7" cy="8" r="3"/><path d="M15 3h4l-1 3h-2zM13 8h8l-1 6h-6z"/><path d="M2 19c4-2 7-2 10 0l7-3"/></svg></div><div class="service__label">DEBT<br>MANAGEMENT</div></div>
    <div class="service" style="left:305px"><div class="service__icon"><svg width="24" height="24" viewBox="0 0 24 24" fill="none" stroke="var(--navy)" stroke-width="1.3"><rect x="10" y="3" width="11" height="11" rx="1.5"/><path d="M15.5 6v5M13 8.5h5"/><rect x="3" y="9" width="8" height="11" rx="1"/><path d="M5 13h4M5 16h4"/></svg></div><div class="service__label">EMERGENCY<br>FUND</div></div>
    <div class="service" style="left:379px"><div class="service__icon"><svg width="24" height="24" viewBox="0 0 24 24" fill="none" stroke="var(--navy)" stroke-width="1.3"><path d="M14 6l-2-3h6l-2 3c4 2 6 6 6 10a4 4 0 0 1-4 4h-4"/><rect x="3" y="16" width="9" height="3"/><rect x="4" y="13" width="9" height="3"/><rect x="3" y="10" width="9" height="3"/></svg></div><div class="service__label">BUILD WEALTH</div></div>
    <div class="service" style="left:454px"><div class="service__icon"><svg width="24" height="24" viewBox="0 0 24 24" fill="none" stroke="var(--navy)" stroke-width="1.3"><path d="M9 3h5M10 3v6l-5 10a1 1 0 0 0 1 2h9"/><circle cx="17" cy="17" r="4"/><path d="M15.5 15.5l3 3M18.5 15.5l-3 3"/></svg></div><div class="service__label">PRESERVE</div></div>
  </section>

  <h2 class="section-title" style="left:144px;top:486px">
    <i class="rule"></i><b>HOW ARE</b><span>WE DOING IT?</span><i class="rule"></i>
  </h2>

  <div class="tag" style="left:48px;top:522px;width:112px">Living&nbsp; Expenses</div>
  <div class="tag" style="left:167px;top:522px;width:75px">Taxes</div>
  <div class="tag" style="left:248px;top:521px;width:75px">Debt</div>

  <svg class="abs" style="left:0;top:540px" width="545" height="135" viewBox="0 0 545 135" fill="none" stroke="var(--navy)" stroke-width=".7" stroke-dasharray="2 1.5">
    <path d="M101 6v16h183V6M201 6v43"/>
    <path d="M198 46l3 4 3-4" stroke-dasharray="none" stroke="var(--green)"/>
    <path d="M198 113v15h144"/>
    <path d="M339 125l3 3-3 3" stroke-dasharray="none" stroke="var(--green)"/>
  </svg>

  <div class="savings-label">Savings</div>
  <div class="goals">
    <div class="goal"><i></i>Retirement Savings</div>
    <div class="goal"><i></i>Children's Education</div>
    <div class="goal"><i></i>Proper Protection</div>
    <div class="goal"><i></i>Freedom From Debt</div>
  </div>

  <div class="partner partner--c1" style="top:523px">Maplecrest</div>
  <div class="partner partner--c2" style="top:523px">Northfield Life</div>
  <div class="partner partner--c1" style="top:555px">Daybreak Financial</div>
  <div class="partner partner--c2" style="top:555px">Lakeshore Mutual</div>
  <div class="partner partner--c1" style="top:587px">Harborline Group</div>
  <div class="partner partner--c2" style="top:587px">Granite Insurance</div>
  <div class="partner partner--c1" style="top:619px">Veridia</div>
  <div class="partner partner--c2" style="top:619px">Summit Insurance</div>
  <div class="partner partner--c1" style="top:651px">Unityfold</div>
  <div class="partner partner--c2" style="top:651px">Corvane</div>
</section>

<!-- ================= RIGHT PAGE ================= -->
<section class="page page--right">
  <svg class="header-shapes" width="545" height="80" viewBox="0 0 545 80">
    <polygon points="0,0 430,0 0,76" fill="var(--navy)"/>
    <polygon points="283,28 430,0 545,0 545,76" fill="var(--green)"/>
  </svg>
  <div class="brand" style="top:17px">
    <div class="brand__name">KESTRELWAY</div>
    <div class="brand__sub">FINANCIAL PLANS</div>
  </div>

  <h2 class="section-title" style="left:33px;top:78px">
    <i class="rule"></i><b>RULE</b><span>OF 72</span>
  </h2>

  <div class="rule-col" style="left:33px">
    <div class="rule-col__head">MONEY DOUBLES<br>EVERY 18 YEARS</div>
    <div class="growth">
      <div class="growth__head"><span>AGE</span><span>4%</span></div>
      <div>
        <div class="growth__row" style="background:var(--navy)"><span>29</span><span>$10,000</span></div>
        <div class="growth__row" style="background:var(--green)"><span>47</span><span>$20,000</span></div>
        <div class="growth__row" style="background:var(--navy)"><span>65</span><span>$40,000</span></div>
      </div>
    </div>
  </div>

  <div class="rule-col" style="left:155px">
    <div class="rule-col__head">MONEY DOUBLES<br>EVERY 12 YEARS</div>
    <div class="growth" style="padding-bottom:14px">
      <div class="growth__head"><span>AGE</span><span>6%</span></div>
      <div>
        <div class="growth__row" style="background:var(--navy)"><span>29</span><span>$10,000</span></div>
        <div class="growth__row" style="background:var(--green)"><span>41</span><span>$20,000</span></div>
        <div class="growth__row" style="background:var(--navy)"><span>53</span><span>$40,000</span></div>
        <div class="growth__row" style="background:var(--green)"><span>65</span><span>$80,000</span></div>
      </div>
    </div>
  </div>

  <div class="rule-col" style="left:277px">
    <div class="rule-col__head">MONEY DOUBLES<br>EVERY 9 YEARS</div>
    <div class="growth">
      <div class="growth__head"><span>AGE</span><span>4%</span></div>
      <div>
        <div class="growth__row" style="background:var(--navy)"><span>29</span><span>$10,000</span></div>
        <div class="growth__row" style="background:var(--green)"><span>38</span><span>$20,000</span></div>
        <div class="growth__row" style="background:var(--navy)"><span>47</span><span>$40,000</span></div>
        <div class="growth__row" style="background:var(--green)"><span>56</span><span>$80,000</span></div>
        <div class="growth__row" style="background:var(--navy)"><span>65</span><span>$1,60,000</span></div>
      </div>
    </div>
  </div>

  <div class="rule-col" style="left:398px">
    <div class="rule-col__head">MONEY DOUBLES<br>EVERY 6 YEARS</div>
    <div class="growth">
      <div class="growth__head"><span>AGE</span><span>4%</span></div>
      <div>
        <div class="growth__row" style="background:var(--navy)"><span>29</span><span>$10,000</span></div>
        <div class="growth__row" style="background:var(--green)"><span>35</span><span>$20,000</span></div>
        <div class="growth__row" style="background:var(--navy)"><span>41</span><span>$40,000</span></div>
        <div class="growth__row" style="background:var(--green)"><span>47</span><span>$80,000</span></div>
        <div class="growth__row" style="background:var(--navy)"><span>53</span><span>$1,60,000</span></div>
        <div class="growth__row" style="background:var(--green)"><span>59</span><span>$320,000</span></div>
        <div class="growth__row" style="background:var(--navy)"><span>65</span><span>$640,000</span></div>
      </div>
    </div>
  </div>

  <h2 class="section-title" style="left:33px;top:332px">
    <i class="rule"></i><b>TAXES</b>
  </h2>

  <div class="tax-board">
    <svg class="abs" style="left:0;top:0" width="477" height="150" viewBox="0 0 477 150">
      <polygon points="0,17 60,0 122,17 184,0 239,17 299,0 356,17 416,0 477,17 477,150 0,150" fill="var(--navy)"/>
    </svg>
    <div class="tax-cols">
      <div class="tax-col">
        <div class="tax-col__title">Home</div>
        <div class="tax-col__body"><p>Partner with Mortgage Brokers for Best Rates</p><p>Mortgage Insurance Alternatives</p></div>
      </div>
      <div class="tax-col">
        <div class="tax-col__title">RRSP</div>
        <div class="tax-col__body"><p>Tax Deduction</p><p>Tax Deferred</p></div>
      </div>
      <div class="tax-col">
        <div class="tax-col__title">TFSA</div>
        <div class="tax-col__body tight"><p>No Tax Deductions</p><p>Tax Free Growth</p><p>2009- $95,000</p><p>Limit 2023 - $7,000/yr</p></div>
      </div>
      <div class="tax-col">
        <div class="tax-col__title">PERM LIFE</div>
        <div class="tax-col__body"><p>No Tax Deduction<br>Qualify<br>Tax Deferred Growth</p></div>
      </div>
    </div>
    <div class="tax-result">
      <div>SELL</div><div>100% TAX</div><div>0% TAX</div><div>0% TAX</div>
    </div>
    <div class="tax-protect">
      <div>Life Insurance Illness<br>Critical / Disability</div>
      <div>Debt management<br>Cash Flow</div>
    </div>
  </div>

  <svg class="abs" style="left:0;top:620px" width="545" height="85" viewBox="0 0 545 85">
    <polygon points="0,4 258,48 98,85 0,85" fill="var(--green)"/>
    <polygon points="545,4 545,85 98,85" fill="var(--navy)"/>
  </svg>
</section>

</body>
</html>
```